Water ATM Card

Need a design for water ATM cards. Size of card is 3.375 x 2.125 inch
On the Front include the Cedar hollow Logo.
Bottom right corner should have Price $100
On the Back
This card is to be used to access water refills at any Cedar Hollow Water Vending Machines.
Please contact (869) 418 2930 or (869) 534 1276 or email clearflowbox@mailvista.example for any assistance or recharging of card.

```html
<!DOCTYPE html>
<html lang="en">
<head>
<meta charset="utf-8">
<title>Cedar Hollow Water Card</title>
<link rel="stylesheet" href="https://fonts.googleapis.com/css2?family=Poppins:ital,wght@0,400;0,600;0,700;1,400;1,700&display=swap">
<style>
  :root {
    --stage: #2d2d2d;
    --brand-blue: #1f6fc0;
    --deep-blue: #1a5ea6;
    --water-blue: #2a7fba;
    --mist: #f4f8f7;
    --forest: #4f8f3a;
    --sky: #8fc3e6;
    --white: #ffffff;
  }
  * { box-sizing: border-box; margin: 0; padding: 0; }
  html, body { width: 1200px; height: 866px; overflow: hidden; }
  body {
    background: var(--stage);
    font-family: "Poppins", sans-serif;
    display: flex;
    align-items: center;
    justify-content: center;
    gap: 40px;
  }
  .card {
    position: relative;
    width: 540px;
    height: 340px;
    border-radius: 6px;
    overflow: hidden;
    background: var(--mist);
    box-shadow: 0 10px 28px rgba(0,0,0,.45);
  }
  .scenery {
    position: absolute;
    inset: 0;
    background:
      linear-gradient(180deg, var(--sky) 0%, #b9dcef 12%, var(--forest) 26%, #6fa34f 42%, #cfe3dc 54%, var(--water-blue) 70%, var(--deep-blue) 100%);
  }
  /* Front */
  .card--front .mist-fade {
    position: absolute;
    inset: 0;
    background: linear-gradient(20deg, rgba(255,255,255,.97) 0%, rgba(244,248,247,.9) 38%, rgba(244,248,247,.55) 55%, rgba(255,255,255,0) 75%);
  }
  .brand {
    position: absolute;
    left: 34px;
    top: 150px;
    display: flex;
    align-items: center;
    gap: 12px;
  }
  .brand-dot {
    width: 22px; height: 22px;
    border-radius: 50%;
    background: var(--brand-blue);
  }
  .brand-name {
    font-weight: 700;
    font-size: 34px;
    letter-spacing: 1px;
    color: var(--brand-blue);
    text-transform: uppercase;
    line-height: 1;
  }
  .tagline {
    position: absolute;
    left: 68px;
    top: 194px;
    font-size: 17px;
    letter-spacing: 1.5px;
    color: var(--brand-blue);
  }
  .price-tag {
    position: absolute;
    right: 0;
    bottom: 30px;
    padding: 9px 22px 9px 26px;
    background: var(--brand-blue);
    color: var(--white);
    border-radius: 24px 0 0 24px;
    font-weight: 700;
    font-size: 22px;
    letter-spacing: 1px;
  }
  /* Back */
  .card--back .mist-fade {
    position: absolute;
    inset: 0;
    background: linear-gradient(180deg, rgba(255,255,255,1) 0%, rgba(255,255,255,.85) 22%, rgba(255,255,255,0) 42%);
  }
  .usage-note {
    position: absolute;
    top: 26px;
    right: 26px;
    width: 400px;
    text-align: right;
    font-weight: 700;
    font-size: 15px;
    line-height: 1.35;
    color: var(--brand-blue);
    text-transform: uppercase;
  }
  .contact {
    position: absolute;
    left: 26px;
    right: 20px;
    bottom: 26px;
    color: var(--white);
  }
  .contact-lead {
    font-weight: 600;
    font-size: 12px;
    text-align: right;
    margin-right: 70px;
  }
  .contact-phones {
    font-weight: 600;
    font-size: 21px;
    letter-spacing: .5px;
  }
  .contact-phones small, .contact-mail small { font-size: 12px; font-weight: 400; }
  .contact-mail {
    font-weight: 700;
    font-style: italic;
    font-size: 20px;
  }
  .contact-note { font-size: 13px; margin-top: 2px; }
</style>
</head>
<body>
  <section class="card card--front">
    <div class="scenery" role="img" aria-label="Photo of tiered waterfalls over a lake with forested hills"></div>
    <div class="mist-fade"></div>
    <div class="brand">
      <span class="brand-dot"></span>
      <span class="brand-name">Cedar Hollow</span>
    </div>
    <p class="tagline">Purified Spring Water</p>
    <p class="price-tag">PRICE $100</p>
  </section>

  <section class="card card--back">
    <div class="scenery" role="img" aria-label="Photo of tiered waterfalls over a lake with forested hills"></div>
    <div class="mist-fade"></div>
    <p class="usage-note">This card is to be used to access water refills at any Cedar Hollow water vending machines</p>
    <div class="contact">
      <p class="contact-lead">Please contact</p>
      <p class="contact-phones">(869) 418 2930 <small>or</small> (869) 534 1276</p>
      <p class="contact-mail"><small>or</small> clearflowbox@mailvista.example</p>
      <p class="contact-note">for any assistance or recharging of card</p>
    </div>
  </section>
</body>
</html>
```